Visitenkarten für Mentorin für Frauen
Zielgruppe
Ich bin Mentorin für Frauen (30-50 Jahre alt), die ihre Berufung endlich finden möchten und sich nach mehr Energie und Sinn sehnen. Ich helfe ihnen mit meiner (Name fehtl noch)-Methode ihren Seelenweg zu finden und zu gehen, sodass sie vor Energie übersprudeln und mit einem Leuchten in den Augen ein Leben in Fluss und Fülle kreieren.
Sie sind nicht unglücklich, aber es fehtl ihnen was, das sie wirklich erfüllt.
Stichwörter: Numerologie, Human Design, Seelenweg, Berufung, Lebensaufgabe, erfüllt sein- endlich die Leere füllen, Freiheit, Selbstbestimmt, Selbstliebe, Potentialentfaltung, Transformation
meine core story:
Mit Freude, unglaublicher Energie und einem Strahlen in den Augen schon vor dem Wecker aufzustehen, war für mich früher undenkbar. Ich konnte mir nicht vorstellen, wie sich Leute auf den Montag freuen konnten.
Dabei hätte mich nicht als unglücklich bezeichnet, aber es fehlt einfach etwas, ich hatte eine innere Leere und eine Sehnsucht nach dem Sinn in meinem Lebe, wollte so geliebt werden wie ich bin und mich auch so zeigen können. Ich weiß wie es ist sich klein, unsicher zu fühlen und nicht zu wissen woher das kommt. Ich habe es einfach nicht für möglich gehalten, dass diese innere Leere so leicht zu füllen ist und Freude, Spaß, Selbstbewusstseein und Leichtigkeit in allen Bereichen mit sich bringt.
Weil ich selbst diesen Weg gegangen bin und weil ich weiß, dass es nichts erfüllenderes gibt als das schlummernde Potential zu erwecken, begleite ich Frauen dabei ihren Seelenweg zu finden und zu gehen.
Dadurch dass sie genau wissen, was ihre Gaben sind und was ihre Seele glücklich macht, haben sie Spaß und Freude, gerade auch in den alltäglichen Dingen. Sie führen ein selbstbestimmtes Leben, lieben sich selbst und zeigen sich so wie sie sind.Die gigantische Energie die dadurch in ihnen frei wird, lässt sie die bisherigen Grenzen überwinden. Sie tun was sie erfüllt, o..
Aufgabenstellung
weiblich, geschwungen, weich: beinhalten solls:
Marlene Wittberg
Mentorin für Powerfrauen
(Lebe deine Berufung)--> da bin ich mir nicht ganz sicher ob das gut aussehn wird oder zuviel wird
falls relevant habe ich bisher folgende Schriftarten verwendet: Canva Sans und Tan mon cheri
ist aber kein muss

```html
<!DOCTYPE html>
<html lang="de">
<head>
<meta charset="UTF-8">
<title>Visitenkarte – Marlene Wittberg</title>
<link rel="stylesheet" href="https://fonts.googleapis.com/css2?family=Italiana&family=Montserrat:wght@400;500&display=swap">
<style>
  :root {
    --paper: #f3f0eb;
    --gold: #b07e44;
    --blush: #f3c2c0;
    --blush-light: #f7dcd6;
  }
  * { margin: 0; padding: 0; box-sizing: border-box; }
  html, body {
    width: 1200px;
    height: 686px;
    overflow: hidden;
    background: var(--paper);
  }
  .card {
    position: relative;
    width: 1200px;
    height: 686px;
    background: var(--paper);
    color: var(--gold);
    font-family: "Montserrat", sans-serif;
  }
  .artwork {
    position: absolute;
    left: 88px;
    top: 112px;
    width: 360px;
    height: 460px;
  }
  .name {
    position: absolute;
    left: 537px;
    top: 112px;
    font-family: "Italiana", serif;
    font-weight: 400;
    font-size: 62px;
    letter-spacing: 0.01em;
    line-height: 1;
    text-transform: uppercase;
    white-space: nowrap;
  }
  .role {
    position: absolute;
    left: 538px;
    top: 190px;
    font-size: 31px;
    font-weight: 400;
    letter-spacing: 0.36em;
    line-height: 59px;
    text-transform: uppercase;
  }
  .contacts {
    position: absolute;
    left: 536px;
    top: 318px;
    list-style: none;
  }
  .contact {
    display: flex;
    align-items: center;
    height: 46px;
    margin-bottom: 28px;
    font-size: 30px;
    font-weight: 400;
    white-space: nowrap;
  }
  .contact-icon {
    width: 38px;
    height: 38px;
    margin-right: 40px;
    flex: none;
    fill: var(--gold);
  }
  .contact-icon.outline { fill: none; stroke: var(--gold); stroke-width: 1.6; }
</style>
</head>
<body>
<div class="card">
  <svg class="artwork" viewBox="0 0 360 460" role="img" aria-label="Illustration: drei feine goldene Schmetterlinge auf zartrosa Farbflecken mit kleinen Punkten">
    <defs>
      <linearGradient id="blushFade" x1="0" y1="0" x2="1" y2="1">
        <stop offset="0" stop-color="#f7dcd6"/>
        <stop offset="0.6" stop-color="#f3c2c0"/>
        <stop offset="1" stop-color="#f7dcd6"/>
      </linearGradient>
    </defs>
    <path fill="url(#blushFade)" d="M110 60 C160 30 230 60 240 110 C300 100 330 150 300 200 C360 250 350 350 290 390 C240 440 170 440 130 400 C70 410 10 370 5 300 C0 240 40 200 90 200 C50 160 60 90 110 60 Z"/>
  </svg>

  <h1 class="name">Marlene Wittberg</h1>
  <p class="role">Mentorin für<br>Powerfrauen</p>

  <ul class="contacts">
    <li class="contact">
      <svg class="contact-icon" viewBox="0 0 24 24" aria-hidden="true"><path d="M6.6 10.8c1.4 2.8 3.8 5.1 6.6 6.6l2.2-2.2c.3-.3.7-.4 1-.2 1.1.4 2.3.6 3.6.6.6 0 1 .4 1 1V20c0 .6-.4 1-1 1C10.6 21 3 13.4 3 4c0-.6.4-1 1-1h3.5c.6 0 1 .4 1 1 0 1.3.2 2.5.6 3.6.1.3 0 .7-.2 1L6.6 10.8z"/></svg>
      <span>+49 151 2468 1357</span>
    </li>
    <li class="contact">
      <svg class="contact-icon" viewBox="0 0 24 24" aria-hidden="true"><path d="M12 2 2 8.5V21h20V8.5L12 2zm0 2.4 7.6 4.9L12 14 4.4 9.3 12 4.4zM4 11.2l8 5 8-5V19H4v-7.8z"/></svg>
      <span>hallo@seelenweg-mentoring.de</span>
    </li>
    <li class="contact">
      <svg class="contact-icon" viewBox="0 0 24 24" aria-hidden="true"><path d="M12 2a7 7 0 0 0-7 7c0 5.2 7 13 7 13s7-7.8 7-13a7 7 0 0 0-7-7zm0 9.5A2.5 2.5 0 1 1 12 6.5a2.5 2.5 0 0 1 0 5z"/></svg>
      <span>Lindenallee 12, Musterstadt</span>
    </li>
    <li class="contact">
      <svg class="contact-icon outline" viewBox="0 0 24 24" aria-hidden="true"><circle cx="12" cy="12" r="9.5"/><ellipse cx="12" cy="12" rx="4.2" ry="9.5"/><path d="M2.5 12h19M4 7h16M4 17h16"/></svg>
      <span>www.seelenweg-mentoring.de</span>
    </li>
  </ul>
</div>
</body>
</html>
```